SkyvornQ Business Cards and Stationary Design

Need a design for our business cards and stationary. I want to carry on the theme of the logo. I want the business cards to have a design on the back. I would like the business cards and the stationary to carry the same theme, design scheme, and branding

Target Market(s)

Airlines and Maintenance Facilities

Industry/Entity Type

Aviation

Contact Information for Business Card

Name
Position Title
Address: 4827 Trellis Hollow Road, Fort Pierce, Florida, 34951
Office Number
Mobile Number
Email
Website

Font styles to use
Serif
Sans Serif

Colors

Designer to choose colors to be used in the design.

```html
<!DOCTYPE html>
<html lang="en">
<head>
<meta charset="utf-8">
<title>SkyvornQ Business Cards</title>
<link rel="stylesheet" href="https://fonts.googleapis.com/css2?family=PT+Sans:wght@400;700&display=swap">
<style>
  :root {
    --page-bg: #e9ebee;
    --card-white: #ffffff;
    --navy: #142c5c;
    --navy-deep: #0d2a5e;
    --sky: #1a9be0;
    --royal: #0b55a8;
    --text-grey: #4a5563;
    --shadow: rgba(15, 30, 60, 0.18);
  }
  * { box-sizing: border-box; margin: 0; padding: 0; }
  html, body { width: 1200px; height: 872px; overflow: hidden; }
  body {
    background: var(--page-bg);
    display: flex;
    align-items: center;
    justify-content: center;
    gap: 40px;
    font-family: "PT Sans", sans-serif;
  }
  .card {
    position: relative;
    width: 560px;
    height: 320px;
    background: var(--card-white);
    box-shadow: 0 10px 30px var(--shadow);
    overflow: hidden;
  }

  .brand-name {
    font-family: "PT Sans", sans-serif;
    font-weight: 700;
    color: var(--navy);
    letter-spacing: 0;
    line-height: 1;
  }
  .brand-dot {
    display: inline-block;
    background: var(--royal);
    flex: none;
  }

  /* Front: brand side */
  .card--front .brand-block {
    position: absolute;
    left: 0;
    right: 0;
    top: 0;
    bottom: 0;
    display: flex;
    flex-direction: column;
    align-items: center;
    justify-content: center;
    gap: 12px;
  }
  .card--front .brand-line { display: flex; align-items: center; gap: 16px; }
  .card--front .brand-dot { width: 26px; height: 26px; }
  .card--front .brand-name { font-size: 52px; }
  .card--front .brand-url {
    font-size: 15px;
    letter-spacing: 0.08em;
    color: var(--text-grey);
  }

  /* Back: contact side */
  .card--back .wave { position: absolute; inset: 0; width: 100%; height: 100%; }
  .card--back .brand-line {
    position: absolute;
    left: 40px;
    top: 142px;
    display: flex;
    align-items: center;
    gap: 12px;
  }
  .card--back .brand-dot { width: 18px; height: 18px; }
  .card--back .brand-name { font-size: 36px; }
  .contact {
    position: absolute;
    right: 26px;
    top: 50px;
    width: 210px;
    color: #fff;
    text-align: right;
  }
  .contact__name {
    font-weight: 700;
    font-size: 21px;
    text-transform: uppercase;
  }
  .contact__title {
    font-size: 18px;
    text-transform: uppercase;
    opacity: 0.85;
    margin-bottom: 22px;
  }
  .contact__list { list-style: none; font-size: 14px; line-height: 24px; }
  .contact__list li { display: flex; align-items: center; justify-content: flex-end; gap: 6px; }
  .contact__list svg { width: 13px; height: 13px; flex: none; }
  .contact__list .address { margin-top: 10px; align-items: flex-start; line-height: 19px; }
  .contact__list .address svg { margin-top: 3px; }
</style>
</head>
<body>

<section class="card card--front" aria-label="Business card front">
  <div class="brand-block">
    <div class="brand-line">
      <span class="brand-dot" aria-hidden="true"></span>
      <span class="brand-name">SkyvornQ</span>
    </div>
    <div class="brand-url">www.skyvornq.com</div>
  </div>
</section>

<section class="card card--back" aria-label="Business card back">
  <svg class="wave" viewBox="0 0 560 320" preserveAspectRatio="none" aria-hidden="true">
    <defs>
      <linearGradient id="blueField" x1="0" y1="0" x2="1" y2="1">
        <stop offset="0" stop-color="#1a9be0"/>
        <stop offset="1" stop-color="#0b55a8"/>
      </linearGradient>
    </defs>
    <path d="M255 0 C345 60 345 210 235 320 L560 320 L560 0 Z" fill="#0d2a5e"/>
    <path d="M292 0 C370 70 360 220 262 320 L560 320 L560 0 Z" fill="url(#blueField)"/>
  </svg>

  <div class="brand-line">
    <span class="brand-dot" aria-hidden="true"></span>
    <span class="brand-name">SkyvornQ</span>
  </div>

  <div class="contact">
    <div class="contact__name">Dorian Velkamp</div>
    <div class="contact__title">President</div>
    <ul class="contact__list">
      <li>
        <svg viewBox="0 0 16 16" aria-hidden="true"><circle cx="8" cy="8" r="7" fill="none" stroke="#fff" stroke-width="1.4"/><path d="M5.5 4.5 L7 6 L6.2 7 Q7 9 9 9.8 L10 9 L11.5 10.5 L10.6 11.5 Q6 11 4.5 5.4 Z" fill="#fff"/></svg>
        012-345-6789
      </li>
      <li>
        <svg viewBox="0 0 16 16" aria-hidden="true"><circle cx="8" cy="8" r="7" fill="none" stroke="#fff" stroke-width="1.4"/><rect x="5.5" y="4" width="5" height="8" rx="1" fill="none" stroke="#fff" stroke-width="1.2"/></svg>
        012-345-6789
      </li>
      <li>
        <svg viewBox="0 0 16 16" aria-hidden="true"><circle cx="8" cy="8" r="7" fill="none" stroke="#fff" stroke-width="1.4"/><rect x="4.5" y="5.5" width="7" height="5" fill="none" stroke="#fff" stroke-width="1.1"/><path d="M4.5 5.5 L8 8.3 L11.5 5.5" fill="none" stroke="#fff" stroke-width="1.1"/></svg>
        info@skyvornq.com
      </li>
      <li>
        <svg viewBox="0 0 16 16" aria-hidden="true"><circle cx="8" cy="8" r="7" fill="none" stroke="#fff" stroke-width="1.4"/><ellipse cx="8" cy="8" rx="3" ry="7" fill="none" stroke="#fff" stroke-width="1.1"/><path d="M1 8 H15 M2.5 4.5 H13.5 M2.5 11.5 H13.5" stroke="#fff" stroke-width="1.1"/></svg>
        www.skyvornq.com
      </li>
      <li class="address">
        <svg viewBox="0 0 16 16" aria-hidden="true"><circle cx="8" cy="8" r="7" fill="none" stroke="#fff" stroke-width="1.4"/><path d="M8 12.5 Q4.8 8.8 4.8 6.8 A3.2 3.2 0 0 1 11.2 6.8 Q11.2 8.8 8 12.5 Z" fill="none" stroke="#fff" stroke-width="1.1"/><circle cx="8" cy="6.8" r="1.1" fill="#fff"/></svg>
        <span>Street Name, City Name<br>Zipcode-012345</span>
      </li>
    </ul>
  </div>
</section>

</body>
</html>
```